CM Candle Tube Packaging Design

Website: www.corvelmare.example
IG: @corvel.mare
Tagline: Elevate Your Ambiance
My brand is a sophisticated brand with luxury candles made of coconut wax. Im looking for an upscale minimalist chic design.
Discover the transformative power of positive energy with Corvel Mare candles. Indulge in true luxury with our specially crafted coconut wax blend that not only ignites captivating scents but also embodies modern elegance and empowering elements.
At Corvel Mare we're committed to delivering a unique and exhilarating aromatic experience to all candle lovers. Each candle is meticulously handcrafted in small batches using luxury fragrance oils exclusively formulated for coconut wax.
Our candles are:
Clean-burning
Paraben-Free
Phthalate-Free
Skin-Safe
Pet-Friendly

```html
<!DOCTYPE html>
<html lang="en">
<head>
<meta charset="utf-8">
<title>Corvel Mare – Candle Tube Packaging</title>
<link href="https://fonts.googleapis.com/css2?family=Josefin+Sans:wght@300;400&family=Cormorant+Garamond:wght@600&family=Montserrat:wght@400;500&family=Great+Vibes&display=swap" rel="stylesheet">
<style>
  :root {
    --backdrop: #c4c6cf;
    --sage: #a8b8ad;
    --sage-light: #b7c5bb;
    --ink: #1e2320;
    --rule: #4a524d;
    --rim: #eceae6;
  }
  * { margin: 0; padding: 0; box-sizing: border-box; }
  html, body {
    width: 1200px; height: 884px; overflow: hidden;
    background: var(--backdrop);
  }
  .canvas { position: relative; width: 1200px; height: 884px; }

  /* Tube wrap label, laid flat */
  .tube-wrap {
    position: absolute; left: 290px; top: 150px;
    width: 380px; height: 560px;
    background: linear-gradient(90deg, var(--sage-light), var(--sage) 60%, #9aab9f);
    display: flex; flex-direction: column; align-items: center;
    color: var(--ink);
  }
  .brand-name {
    margin-top: 58px;
    font-family: "Josefin Sans", sans-serif; font-weight: 300;
    font-size: 36px; letter-spacing: 1px;
  }
  .brand-line {
    margin-top: 14px; display: flex; align-items: center; gap: 12px;
    font-family: "Montserrat", sans-serif; font-size: 10.5px; letter-spacing: 4px;
  }
  .brand-line::before, .brand-line::after {
    content: ""; width: 20px; height: 1px; background: var(--ink);
  }
  .script-line {
    margin-top: 10px;
    font-family: "Great Vibes", cursive; font-size: 14px; color: var(--rule);
  }
  .headline {
    margin-top: 60px; padding: 10px 20px;
    border-top: 1px solid rgba(74,82,77,.45);
    border-bottom: 1px solid rgba(74,82,77,.45);
    font-family: "Cormorant Garamond", serif; font-weight: 600;
    font-size: 25px; line-height: 1; text-align: center; letter-spacing: 1px;
    text-transform: uppercase;
  }
  .badges { margin-top: 60px; display: flex; gap: 30px; }
  .badge { width: 60px; height: 60px; }
  .badge text { font-family: "Montserrat", sans-serif; font-size: 5.5px; fill: var(--ink); }
  .contact {
    margin-top: auto; margin-bottom: 36px; width: 100%;
    padding: 0 48px; display: flex; justify-content: space-between;
    font-family: "Montserrat", sans-serif; font-size: 11.5px;
  }
  .contact .web { font-weight: 500; }

  /* Lid top */
  .lid {
    position: absolute; left: 770px; top: 300px;
    width: 260px; height: 260px; border-radius: 50%;
    background: var(--sage); border: 8px solid var(--rim);
    display: flex; align-items: center; justify-content: center;
  }
  .lid-mark {
    font-family: "Josefin Sans", sans-serif; font-weight: 300;
    font-size: 40px; color: var(--ink); letter-spacing: 2px;
  }
</style>
</head>
<body>
<div class="canvas">
  <section class="tube-wrap">
    <h1 class="brand-name">CORVEL MARE</h1>
    <p class="brand-line">HANDMADE CANDLES</p>
    <p class="script-line">with purpose and love</p>

    <h2 class="headline">Elevate Your<br>Ambiance</h2>

    <div class="badges">
      <svg class="badge" viewBox="0 0 60 60" aria-label="eco-friendly">
        <circle cx="30" cy="28" r="24" fill="none" stroke="#1e2320" stroke-width="0.8"/>
        <circle cx="33" cy="24" r="9" fill="none" stroke="#1e2320" stroke-width="1"/>
        <path d="M24 24h18M33 15v18M26 19h14M26 29h14" stroke="#1e2320" stroke-width="0.7"/>
        <path d="M18 36c2-8 10-10 14-8-3 6-9 9-14 8z" fill="#1e2320"/>
        <text x="30" y="48" text-anchor="middle">eco-friendly</text>
      </svg>
      <svg class="badge" viewBox="0 0 60 60" aria-label="100% natural">
        <circle cx="30" cy="28" r="24" fill="none" stroke="#1e2320" stroke-width="0.8"/>
        <path d="M22 36c0-12 8-18 16-20 0 12-6 19-16 20z" fill="#1e2320"/>
        <path d="M23 35l13-17" stroke="#a8b8ad" stroke-width="1"/>
        <text x="30" y="48" text-anchor="middle">100% natural</text>
      </svg>
      <svg class="badge" viewBox="0 0 60 60" aria-label="vegan">
        <circle cx="30" cy="28" r="24" fill="none" stroke="#1e2320" stroke-width="0.8"/>
        <path d="M30 36c-8-1-12-7-11-14 7 1 11 6 11 14zM30 36c8-1 12-7 11-14-7 1-11 6-11 14z" fill="#1e2320"/>
        <text x="30" y="48" text-anchor="middle">vegan</text>
      </svg>
    </div>

    <div class="contact">
      <span class="handle">@corvel.mare</span>
      <span class="web">www.corvelmare.example</span>
    </div>
  </section>

  <div class="lid">
    <span class="lid-mark">CM</span>
  </div>
</div>
</body>
</html>
```